Tolbek cards

I want a simple business card that pops.
Logo on one side.
On side two i want.
"Are you thinking about a new building on your property, or renovating an existing structure? Contact".....
Owners Name: Dale Whitacre
Owners Phone number: 610-555-0187
Address:4076 Copper Ridge RD, Alder Falls, PA 16830
Committed to Quality, Service, and Integrity

```html
<!DOCTYPE html>
<html lang="en">
<head>
<meta charset="utf-8">
<title>Tolbek Builders – Business Card</title>
<link href="https://fonts.googleapis.com/css2?family=Archivo:wght@400;500;700;800&display=swap" rel="stylesheet">
<style>
  :root {
    --stage: #262626;
    --card: #f2f1ef;
    --brown: #4b3020;
    --tan: #9c8068;
    --tan-light: #c2ab93;
    --ink: #3a2a1f;
    --rule: #b9b2aa;
  }
  * { box-sizing: border-box; margin: 0; padding: 0; }
  html, body {
    width: 1200px; height: 576px; overflow: hidden;
    background: var(--stage);
    font-family: "Archivo", Arial, sans-serif;
  }
  .card {
    position: absolute;
    background: var(--card);
    border-radius: 10px;
    overflow: hidden;
    box-shadow: 0 4px 10px rgba(0,0,0,.45);
  }
  .card-front { left: 102px; top: 139px; width: 484px; height: 292px; }
  .card-back  { left: 596px; top: 138px; width: 480px; height: 291px; }

  .front-name {
    position: absolute; left: 46px; top: 118px;
    color: var(--brown); font-weight: 800; line-height: 1;
  }
  .front-name .word { display: block; font-size: 46px; letter-spacing: -0.5px; }
  .front-name .sub { display: block; font-size: 17px; letter-spacing: 4px; margin-top: 2px; }

  .back-wave { position: absolute; left: 0; top: 0; }
  .question {
    position: absolute; left: 22px; top: 19px; width: 200px;
    color: #f3ece4; font-size: 13px; line-height: 18.5px;
  }
  .contact { position: absolute; left: 22px; top: 169px; width: 200px; }
  .contact-label {
    display: flex; align-items: center; gap: 6px;
    font-size: 9px; color: var(--ink);
  }
  .contact-label::after { content: ""; flex: 1; height: 1px; background: var(--rule); }
  .owner {
    margin-top: 8px; font-size: 19.5px; font-weight: 700; color: var(--ink); letter-spacing: 0.2px;
  }
  .owner .last { color: var(--tan); }
  .detail {
    display: flex; gap: 7px; margin-top: 5px;
    font-size: 12.5px; color: var(--ink); line-height: 1.3;
  }
  .detail svg { flex: none; margin-top: 2px; }

  .brand {
    position: absolute; left: 240px; top: 160px; width: 220px; text-align: center;
    color: var(--brown); font-weight: 800; line-height: 1;
  }
  .brand .word { display: block; font-size: 46px; letter-spacing: -0.5px; }
  .brand .sub { display: block; font-size: 16px; letter-spacing: 2px; margin-top: 3px; }
  .tagline {
    position: absolute; left: 230px; top: 249px; width: 240px; text-align: center;
    font-size: 11.5px; color: var(--ink);
  }
</style>
</head>
<body>

<section class="card card-front" aria-label="Card front">
  <div class="front-name">
    <span class="word">TOLBEK</span>
    <span class="sub">BUILDERS LLC</span>
  </div>
</section>

<section class="card card-back" aria-label="Card back">
  <svg class="back-wave" width="480" height="291" viewBox="0 0 480 291" aria-hidden="true">
    <path d="M0 0 H480 V40 C420 26 360 30 300 62 C230 100 170 140 90 136 C50 134 20 122 0 118 Z" fill="var(--brown)"/>
    <path d="M0 128 C40 140 110 150 170 128 C250 98 300 40 380 24 C420 16 455 20 480 30 V44 C440 30 400 32 350 50 C290 74 240 118 170 140 C110 158 40 150 0 136 Z" fill="var(--tan)"/>
    <path d="M330 30 C380 12 440 14 480 24" stroke="var(--tan-light)" stroke-width="3" fill="none"/>
  </svg>

  <p class="question">Are you thinking about a new<br>building on your property,<br>or renovating an<br>existing structure?</p>

  <div class="contact">
    <p class="contact-label">Contact:</p>
    <p class="owner">DALE <span class="last">WHITACRE</span></p>
    <p class="detail">
      <svg width="11" height="11" viewBox="0 0 24 24" aria-hidden="true"><circle cx="12" cy="12" r="10.5" fill="none" stroke="var(--tan)" stroke-width="2"/><path d="M8.5 7c-.8.8-.7 2.6 1 4.6 1.8 2 3.6 3 4.6 2.2l1-1-2-1.6-1 .8c-.8-.3-1.8-1.3-2.2-2.2l.8-1L9.6 6.8z" fill="var(--tan)"/></svg>
      <span>610-555-0187</span>
    </p>
    <p class="detail">
      <svg width="11" height="11" viewBox="0 0 24 24" aria-hidden="true"><circle cx="12" cy="12" r="10.5" fill="none" stroke="var(--tan)" stroke-width="2"/><path d="M12 5.5a4 4 0 0 0-4 4c0 3 4 7.5 4 7.5s4-4.5 4-7.5a4 4 0 0 0-4-4zm0 5.5a1.5 1.5 0 1 1 0-3 1.5 1.5 0 0 1 0 3z" fill="var(--tan)"/></svg>
      <span>4076 Copper Ridge RD,<br>Alder Falls, PA 16830</span>
    </p>
  </div>

  <div class="brand">
    <span class="word">TOLBEK</span>
    <span class="sub">BUILDERS LLC</span>
  </div>
  <p class="tagline">Committed to Quality, Service &amp; Integrity</p>
</section>

</body>
</html>
```